Need Business Card for eLearning Company

Need a business card designed for our company, CareerVantly.

CareerVantly has developed a complete 12 lesson eLearning course to teach you the skills you need to present yourself in a job interview. The course uses advanced learning techniques in the multimedia videos, plus contains quizzes and additional exercises to insure you get the course and can walk into any interview with confidence and ease, and get the job.

www.careervantly-example.com

Industry/Entity Type

Business

```html
<!DOCTYPE html>
<html lang="en">
<head>
<meta charset="utf-8">
<title>CareerVantly Business Card</title>
<link rel="stylesheet" href="https://fonts.googleapis.com/css2?family=Montserrat:wght@400;700&family=Questrial&display=swap">
<style>
  :root {
    --stage: #1b1b1d;
    --purple: #9a1f86;
    --green: #8db42a;
    --ink: #3a3a3a;
    --grey: #555555;
    --paper: #ffffff;
  }
  * { box-sizing: border-box; margin: 0; padding: 0; }
  html, body { width: 1200px; height: 675px; overflow: hidden; }
  body {
    background: var(--stage);
    display: flex;
    align-items: center;
    justify-content: center;
    gap: 56px;
    font-family: "Questrial", sans-serif;
  }
  .card {
    position: relative;
    width: 525px;
    height: 300px;
    overflow: hidden;
    border-radius: 2px;
  }

  /* Front */
  .card--front { background: var(--paper); color: var(--grey); }
  .front__art {
    position: absolute;
    right: 0;
    top: 0;
    width: 220px;
    height: 300px;
    background: linear-gradient(180deg, rgba(141,180,42,0.35) 0%, rgba(154,31,134,0.28) 45%, rgba(80,80,80,0.55) 100%);
  }
  .front__edge-dot {
    position: absolute;
    left: -26px;
    top: 152px;
    width: 52px;
    height: 52px;
    border-radius: 50%;
    background: var(--purple);
  }
  .brand { position: absolute; }
  .brand__name {
    font-family: "Montserrat", sans-serif;
    font-weight: 400;
    color: var(--ink);
    line-height: 1;
  }
  .card--front .brand { left: 40px; top: 64px; }
  .card--front .brand__name { font-size: 30px; }

  .person { position: absolute; left: 52px; top: 140px; }
  .person__name {
    font-family: "Montserrat", sans-serif;
    font-weight: 700;
    font-size: 15px;
    color: var(--purple);
  }
  .person__title { font-size: 13px; color: var(--grey); margin-top: 1px; }

  .contact { position: absolute; left: 52px; top: 190px; font-size: 11px; line-height: 1.4; color: var(--grey); }
  .contact__line { display: flex; align-items: center; gap: 7px; }
  .contact__address { margin-bottom: 5px; }
  .contact__icon { width: 10px; height: 10px; fill: var(--purple); flex: none; }
  .contact__web {
    font-family: "Montserrat", sans-serif;
    font-weight: 700;
    font-size: 11px;
    color: var(--purple);
    margin-top: 3px;
  }

  /* Back */
  .card--back { background: var(--purple); color: var(--paper); }
  .card--back .brand {
    left: 0; right: 0; top: 110px;
    display: flex; align-items: center; justify-content: center; gap: 14px;
  }
  .brand__mark { width: 30px; height: 30px; border-radius: 50%; background: var(--paper); flex: none; }
  .card--back .brand__name { font-size: 34px; color: var(--paper); }
  .back__web {
    position: absolute; left: 0; right: 0; top: 196px;
    text-align: center;
    font-family: "Montserrat", sans-serif;
    font-weight: 700;
    font-size: 13px;
  }
</style>
</head>
<body>

<section class="card card--front">
  <div class="front__art" role="img" aria-label="Illustration of green and purple speech bubbles rising above a suit and tie"></div>
  <div class="front__edge-dot"></div>

  <div class="brand">
    <div class="brand__name">careervantly</div>
  </div>

  <div class="person">
    <div class="person__name">Daniel Okafor</div>
    <div class="person__title">Principal</div>
  </div>

  <div class="contact">
    <div class="contact__address">418 Linden Avenue<br>Riverton, IL 60999</div>
    <div class="contact__line">
      <svg class="contact__icon" viewBox="0 0 10 10"><path d="M2 1h2l1 2-1.2 1a5 5 0 0 0 2.2 2.2L7 5l2 1v2a1 1 0 0 1-1 1A7 7 0 0 1 1 2a1 1 0 0 1 1-1z"/></svg>
      <span>555.201.4870</span>
    </div>
    <div class="contact__line">
      <svg class="contact__icon" viewBox="0 0 10 10"><rect x="3" y="0.5" width="4" height="3"/><rect x="0.5" y="3.5" width="9" height="4" rx="1"/><rect x="3" y="6.5" width="4" height="3"/></svg>
      <span>555.201.4871</span>
    </div>
    <div class="contact__line">
      <svg class="contact__icon" viewBox="0 0 10 10"><path d="M0.5 2h9v6h-9z M0.5 2l4.5 3.5L9.5 2" stroke="#fff" stroke-width="0.6"/></svg>
      <span>daniel@careervantly-example.com</span>
    </div>
    <div class="contact__web">www.careervantly-example.com</div>
  </div>
</section>

<section class="card card--back">
  <div class="brand">
    <div class="brand__mark"></div>
    <div class="brand__name">careervantly</div>
  </div>
  <div class="back__web">www.careervantly-example.com</div>
</section>

</body>
</html>
```